Business card for my new company (Accounting firm)

I need a business card for my new business Brightwell Advisory and Ledger SA. Our services are accounting, tax, audit and financial management. Our customers are small companies, start-ups and new companies. The final design has to show financial security, trust and growth. Please find our logo attached to the business card. Text for the business card: Brightwell Advisory and Ledger SA Tomas Varenholt Director and Founder Certified Accountant Tel. 022 418 57 34 tv@clairevalconseil.ch www.clairevalconseil.ch Rue des Vergières 27 1201 Geneva
Target Market(s)
Our customers are small companies, start-ups and new companies.
Industry/Entity Type
Finance And Accounting
Contact Information for Business Card
Claireval Conseil et Comptes SA
Tomas Varenholt
Directeur et Fondateur
Expert-comptable diplômé
Tél. 022 418 57 34
tv@clairevalconseil.ch
www.clairevalconseil.ch
Rue des Vergières 27
1201 Genève

```html
<!DOCTYPE html>
<html lang="fr">
<head>
<meta charset="utf-8">
<title>Claireval Conseil et Comptes SA – Cartes de visite</title>
<link rel="stylesheet" href="https://fonts.googleapis.com/css2?family=Roboto:wght@400;500;700&display=swap">
<style>
  :root {
    --backdrop: #e3e4e6;
    --card-front: #ffffff;
    --card-back: #f3f4f5;
    --ink-dark: #3b3b3d;
    --ink-muted: #55585c;
    --brand-deep: #1c5f96;
    --brand-mid: #1f7cc0;
    --brand-light: #2fa6de;
  }
  * { box-sizing: border-box; margin: 0; padding: 0; }
  html, body {
    width: 1200px; height: 726px; overflow: hidden;
    background: var(--backdrop);
    font-family: "Roboto", Arial, sans-serif;
  }
  .sheet {
    width: 1200px; height: 726px;
    display: flex; align-items: center; justify-content: center; gap: 40px;
  }
  .card {
    position: relative;
    width: 540px; height: 310px;
    box-shadow: 0 2px 6px rgba(0,0,0,0.12);
    overflow: hidden;
  }
  .card--front { background: var(--card-front); }
  .card--back { background: var(--card-back); }

  .wordmark {
    display: flex; align-items: center; gap: 14px;
  }
  .wordmark__square {
    width: 30px; height: 30px; background: var(--brand-mid); flex: none;
  }
  .wordmark__name {
    font-weight: 500; color: var(--ink-dark); line-height: 1.05;
  }

  .card--front .wordmark {
    position: absolute; left: 50%; top: 46%;
    transform: translate(-50%, -50%);
  }
  .card--front .wordmark__name { font-size: 44px; }
  .card--front .wordmark__square { width: 36px; height: 36px; }

  .front__stripe {
    position: absolute; left: 0; right: 0; bottom: 34px; height: 9px;
    background: linear-gradient(90deg, var(--brand-deep), var(--brand-light));
  }

  .card--back .wordmark {
    position: absolute; left: 36px; top: 50%; transform: translateY(-50%);
  }
  .card--back .wordmark__name { font-size: 30px; }
  .card--back .wordmark__square { width: 24px; height: 24px; }

  .contact {
    position: absolute; left: 290px; top: 58px;
    color: var(--ink-muted); font-size: 12.5px; line-height: 1.35;
  }
  .contact__name {
    font-size: 20px; font-weight: 700; color: var(--brand-deep);
    margin-bottom: 6px;
  }
  .contact__roles { margin-bottom: 18px; font-size: 11.5px; }
  .contact__lines { list-style: none; margin-bottom: 14px; }
  .contact__lines li { display: flex; align-items: center; gap: 9px; height: 19px; }
  .contact__icon { width: 12px; height: 12px; flex: none; fill: var(--brand-deep); }
  .contact__address { font-style: normal; padding-left: 21px; }
</style>
</head>
<body>
<main class="sheet">
  <section class="card card--front" aria-label="Recto">
    <div class="wordmark">
      <span class="wordmark__square"></span>
      <span class="wordmark__name">Claireval</span>
    </div>
    <div class="front__stripe"></div>
  </section>

  <section class="card card--back" aria-label="Verso">
    <div class="wordmark">
      <span class="wordmark__square"></span>
      <span class="wordmark__name">Claireval</span>
    </div>
    <div class="contact">
      <p class="contact__name">Tomas Varenholt</p>
      <p class="contact__roles">Directeur et Fondateur<br>Expert-comptable diplômé</p>
      <ul class="contact__lines">
        <li>
          <svg class="contact__icon" viewBox="0 0 24 24" aria-hidden="true"><path d="M6.6 10.8a15 15 0 0 0 6.6 6.6l2.2-2.2c.3-.3.7-.4 1-.2 1.1.4 2.3.6 3.6.6.6 0 1 .4 1 1V20c0 .6-.4 1-1 1A17 17 0 0 1 3 4c0-.6.4-1 1-1h3.5c.6 0 1 .4 1 1 0 1.3.2 2.5.6 3.6.1.3 0 .7-.2 1z"/></svg>
          <span>022 418 57 34</span>
        </li>
        <li>
          <svg class="contact__icon" viewBox="0 0 24 24" aria-hidden="true"><path d="M2 5h20v14H2zm2 2v.5l8 5 8-5V7l-8 5z"/></svg>
          <span>tv@clairevalconseil.ch</span>
        </li>
        <li>
          <svg class="contact__icon" viewBox="0 0 24 24" aria-hidden="true"><path d="M12 2a10 10 0 1 0 0 20 10 10 0 0 0 0-20zm6.9 6h-3a15 15 0 0 0-1.3-3.9A8 8 0 0 1 18.9 8zM12 4c.8 1.2 1.5 2.5 1.9 4h-3.8c.4-1.5 1.1-2.8 1.9-4zM4.3 14a8 8 0 0 1 0-4h3.4a16 16 0 0 0 0 4zm.8 2h3a15 15 0 0 0 1.3 3.9A8 8 0 0 1 5.1 16zm3-8h-3a8 8 0 0 1 4.3-3.9A15 15 0 0 0 8.1 8zM12 20c-.8-1.2-1.5-2.5-1.9-4h3.8c-.4 1.5-1.1 2.8-1.9 4zm2.3-6H9.7a14 14 0 0 1 0-4h4.6a14 14 0 0 1 0 4zm.3 5.9a15 15 0 0 0 1.3-3.9h3a8 8 0 0 1-4.3 3.9zm1.7-5.9a16 16 0 0 0 0-4h3.4a8 8 0 0 1 0 4z"/></svg>
          <span>www.clairevalconseil.ch</span>
        </li>
      </ul>
      <address class="contact__address">Rue des Vergières 27<br>1201 Genève</address>
    </div>
  </section>
</main>
</body>
</html>
```